WTF!!! We need a modern professional website for a business litigation law firm.

We need a modern, clean, professional and uncomplicated website for a new business trial and litigation law firm called "Haverlock Trial Firm PLLC". Website must be mobile optimized for iPad and smartphone. The law firm specializes in counseling and representing large corporations, small businesses and entrepreneurs in and out of the courtroom. Lawyers in the firm serve as Florida counsel and trial counsel to organizations facing claims involving product liability, premises liability, professional liability, vehicle and transportation liability, warranty claims, construction defects and delay claims, complex business disputes, commercial litigation and bid disputes in State and Federal Courts. The website is mainly to provide information about the firm, and should include sections describing the firm, identifying the Industries Served and Areas of Practice ," a separate page identifying the "Professionals", a separate page for "Resources & Advisories," and a traveling "Connect With Us" button a site visitor can click on that will launch an email to the Firm's general email account. The website should allow us to easily modify the content on these pages, and let us add/modify links to external information sources. We will not sell anything or take payments through the website. We do need to be able to easily upload and update photographs of attorneys and add new attorneys names/email hyperlinks as the firm grows. We would like to add developments in the law or success stories easily and quickly, such as through a blog page. On the "Connect With Us" page the website should have hyperlinks to email the Firm, and there should be hyperlinks to email each professional on the "Professionals" page. The website should be viewable on mobile devices without distortion. The law firm focuses on trial work and should have some imagery associated with courtrooms, but the overall theme of the site should be modern, clean, and communicate sophistication and strength. The website should be made in Wordpress. We have uploaded logo files for Haverlock Trial Firm.

Target Market(s)

Corporations and companies that are looking for legal representation. Other attorneys/legal industry.

Industry/Entity Type

Legal Industry

Coding

Coded - Design and coding required

Number of Pages Required

1 page

Font styles to use
Sans Serif

Requirements
Must have
• Simple, clean, sophisticated, modern website that includes the logo, watermark of logo, and the elements described above.
Nice to have
• Pictures of city scape, buildings, courtroom, team members.

```html
<!DOCTYPE html>
<html lang="en">
<head>
<meta charset="utf-8">
<title>Haverlock Trial Firm PLLC</title>
<link href="https://fonts.googleapis.com/css2?family=Inter:wght@400;500;600;700;800&display=swap" rel="stylesheet">
<style>
:root{
  --gold:#c39300;
  --gold-dark:#a87d00;
  --ink:#111111;
  --text:#333333;
  --muted:#555555;
  --light:#f3f3f3;
  --gray:#ececec;
  --white:#ffffff;
}
*{box-sizing:border-box;margin:0;padding:0}
html,body{width:1200px;height:3713px;overflow:hidden}
body{font-family:'Inter',sans-serif;color:var(--ink);background:var(--white);position:relative}
.abs{position:absolute}
.photo{position:absolute}
.btn{position:absolute;background:var(--gold);color:var(--white);font-weight:700;border-radius:30px;display:flex;align-items:center;justify-content:center}
.eyebrow{color:var(--gold);font-weight:600}

/* header */
.topbar{left:0;top:0;width:1200px;height:10px;background:var(--ink)}
.brand{left:72px;top:30px;width:190px;text-align:center}
.brand-mark{width:28px;height:28px;border:3px solid var(--ink);margin:6px auto 14px}
.brand-name{font-size:34px;font-weight:800;letter-spacing:1px;line-height:1}
.brand-sub{font-size:15px;font-weight:700;letter-spacing:5px;margin-top:6px}
.contact-bar{left:540px;top:12px;width:660px;height:78px;background:var(--gray);clip-path:polygon(0 0,100% 0,100% 100%,6% 100%)}
.contact-item{display:flex;align-items:center;gap:12px;top:25px}
.contact-icon{width:44px;height:44px;border-radius:50%;background:var(--ink);display:flex;align-items:center;justify-content:center}
.contact-label{font-size:14px;color:var(--gold)}
.contact-value{font-size:15px;font-weight:700}
.contact-value.big{font-size:21px}
.nav{left:360px;top:116px;display:flex;align-items:center;font-size:15px}
.nav a{color:var(--ink);text-decoration:none;margin-right:36px}
.nav a.active{background:var(--gold);color:var(--white);font-weight:600;padding:11px 22px;border-radius:22px;margin-right:18px}

/* hero */
.hero{left:0;top:174px;width:1200px;height:632px;background:linear-gradient(90deg,#3a2a1e 0%,#5a4330 35%,#6b5440 55%,#4a3a2c 100%)}
.hero-title{left:74px;top:358px;font-size:50px;font-weight:700;color:var(--white);line-height:1.17}
.hero-sub{left:74px;top:482px;font-size:19px;color:var(--white)}
.dots{left:1104px;top:380px}
.dots span{display:block;width:9px;height:9px;border-radius:50%;background:var(--gold);margin-bottom:13px}
.dots span.on{background:var(--white)}

/* about */
.about-frame{left:611px;top:833px;width:589px;height:440px;border:2px solid var(--gold);border-right:none}
.about-photo{left:637px;top:860px;width:563px;height:474px;background:linear-gradient(180deg,#d8a42a,#e6c464 50%,#c9c9c9)}
.about-title{left:76px;top:948px;font-size:42px;font-weight:700}
.body-text{font-size:13px;line-height:18px;color:var(--text)}

/* sections */
.section-head{width:1200px;left:0;text-align:center}
.arrows{display:flex;gap:28px;font-size:22px}
.arrows span:last-child{color:var(--gold)}
.card{position:absolute;width:247px;background:var(--light);text-align:center}
.card .photo{left:0;top:0;width:247px}
.card-title{font-size:18px;font-weight:600;line-height:19px}
.card-line{width:30px;height:2px;background:var(--gold);margin:0 auto}
.card-text{font-size:12px;line-height:18px;color:var(--text)}
.badge{width:42px;height:42px;border-radius:50%;background:var(--gold);color:var(--white);display:flex;align-items:center;justify-content:center;font-weight:700;font-size:22px}

/* blog */
.blog-title{font-size:34px;font-weight:600}
.blog-text{font-size:18px;line-height:22px;color:var(--text)}

/* footer */
.footer{left:0;top:3330px;width:1200px;height:383px;background:var(--ink);color:var(--white)}
.footer a{color:var(--white);text-decoration:none}
.f-links{left:409px;top:3470px;font-size:15px;line-height:36px}
.f-links .active{color:var(--gold);font-weight:600}
.f-head{color:var(--gold);font-size:15px;font-weight:600}
.social{display:flex;gap:12px}
.social span{width:34px;height:34px;border-radius:50%;background:var(--gold)}
</style>
</head>
<body>

<!-- Header -->
<div class="abs topbar"></div>
<div class="abs brand">
  <div class="brand-mark"></div>
  <div class="brand-name">HAVERLOCK</div>
  <div class="brand-sub">TRIAL FIRM</div>
</div>
<div class="abs contact-bar"></div>
<div class="abs contact-item" style="left:614px">
  <div class="contact-icon"><svg width="16" height="12" viewBox="0 0 16 12"><rect x="0.5" y="0.5" width="15" height="11" fill="#c39300"/><path d="M1 1l7 6 7-6" stroke="#111" fill="none"/></svg></div>
  <div><div class="contact-label">Email Us</div><div class="contact-value">info@haverlocktrialfirm.com</div></div>
</div>
<div class="abs contact-item" style="left:908px">
  <div class="contact-icon"><svg width="16" height="16" viewBox="0 0 24 24"><path fill="#c39300" d="M6.6 10.8a15 15 0 006.6 6.6l2.2-2.2a1 1 0 011-.25 11 11 0 003.6.6 1 1 0 011 1V20a1 1 0 01-1 1A17 17 0 013 4a1 1 0 011-1h3.5a1 1 0 011 1 11 11 0 00.6 3.6 1 1 0 01-.25 1z"/></svg></div>
  <div><div class="contact-label">Call us for any query</div><div class="contact-value big">1800 - 555 0143</div></div>
</div>
<nav class="abs nav">
  <a class="active">Home</a><a>About</a><a>Practice Area</a><a>Professionals</a><a>Resources&amp; Advisers</a><a>Blog</a><a style="margin-right:0">Contact</a>
</nav>

<!-- Hero -->
<div class="photo hero" role="img" aria-label="Smiling attorney in a suit standing in a law library"></div>
<svg class="abs" style="left:0;top:690px" width="1200" height="120" viewBox="0 0 1200 120">
  <polygon points="0,116 600,4 1200,116 1200,120 0,120" fill="#c39300"/>
  <polygon points="0,116 600,40 1200,116" fill="#111" opacity="0"/>
  <polygon points="0,120 600,40 1200,120" fill="#ffffff"/>
</svg>
<h1 class="abs hero-title">Haverlock Trial<br>Firm PLLC</h1>
<p class="abs hero-sub">A New Business Trial and Litigation Law Firm</p>
<div class="btn" style="left:72px;top:533px;width:244px;height:46px;font-size:22px">Connect with us</div>
<div class="abs dots"><span></span><span class="on"></span><span class="on"></span><span></span><span></span></div>

<!-- About -->
<div class="abs about-frame"></div>
<div class="photo about-photo" role="img" aria-label="Two professionals walking down a bright glass corridor"></div>
<div class="abs eyebrow" style="left:76px;top:910px;font-size:26px">About Us</div>
<h2 class="abs about-title">Haverlock Trial Firm</h2>
<p class="abs body-text" style="left:76px;top:1008px;width:494px">Lorem ipsum dolor sit amet, consectetur adipiscing elit, sed do eiusmod tempor incididunt ut labore et dolore magna aliqua. Quis ipsum suspendisse ultrices gravida. Risus commodo viverra maecenas accumsan lacus vel facilisis.</p>
<p class="abs body-text" style="left:76px;top:1098px;width:494px">Haverlock Trial Firm PLLC Lorem ipsum dolor sit amet, consectetur adipiscing elit, sed do eiusmod tempor incididunt ut labore et dolore magna aliqua. Quis ipsum suspendisse ultrices gravida. Risus commodo viverra maecenas accumsan lacus vel facilisis. Haverlock Trial Firm PLLC</p>
<div class="btn" style="left:72px;top:1197px;width:121px;height:35px;font-size:14px">Learn More</div>

<!-- Services -->
<svg class="abs" style="left:0;top:1355px" width="1200" height="118" viewBox="0 0 1200 118">
  <polygon points="0,116 600,0 1200,116 600,22" fill="#c39300"/>
</svg>
<div class="abs section-head eyebrow" style="top:1445px;font-size:26px">Practice Areas</div>
<h2 class="abs section-head" style="top:1476px;font-size:40px;font-weight:700">Our Services</h2>
<div class="abs arrows" style="left:1064px;top:1496px"><span>‹</span><span>›</span></div>

<div class="card" style="left:72px;top:1560px;height:392px">
  <div class="photo" style="height:225px;background:linear-gradient(135deg,#2c3540,#7a3a2a 55%,#3a4450)" role="img" aria-label="Damaged car after a road accident"></div>
  <svg class="abs" style="left:0;top:188px" width="247" height="40"><polygon points="0,40 123,0 247,40" fill="#f3f3f3"/></svg>
  <div class="abs badge" style="left:102px;top:78px">+</div>
  <div class="abs card-title" style="left:0;width:247px;top:238px">Vehicle and<br>Transportation Liability</div>
  <div class="abs card-line" style="left:108px;top:292px"></div>
  <div class="abs card-text" style="left:24px;width:199px;top:300px">Lorem ipsum dolor sit amet, consectetur adipiscing elit, sed do eiusmod tempor incididun.</div>
</div>
<div class="card" style="left:341px;top:1560px;height:392px">
  <div class="photo" style="height:225px;background:linear-gradient(135deg,#3b4a66,#c9a46a 60%,#8d6b3e)" role="img" aria-label="Hand stacking wooden blocks reading strategy and vision"></div>
  <svg class="abs" style="left:0;top:188px" width="247" height="40"><polygon points="0,40 123,0 247,40" fill="#f3f3f3"/></svg>
  <div class="abs card-title" style="left:0;width:247px;top:246px">Professional Liability</div>
  <div class="abs card-line" style="left:108px;top:292px"></div>
  <div class="abs card-text" style="left:24px;width:199px;top:300px">Lorem ipsum dolor sit amet, consectetur adipiscing elit, sed do eiusmod tempor incididun.</div>
</div>
<div class="card" style="left:611px;top:1560px;height:392px">
  <div class="photo" style="height:225px;background:linear-gradient(135deg,#1a1a1a,#3a3a2a 50%,#e5d23a)" role="img" aria-label="Sticky notes reading product liability"></div>
  <svg class="abs" style="left:0;top:188px" width="247" height="40"><polygon points="0,40 123,0 247,40" fill="#f3f3f3"/></svg>
  <div class="abs card-title" style="left:0;width:247px;top:246px">Product Liability</div>
  <div class="abs card-line" style="left:108px;top:292px"></div>
  <div class="abs card-text" style="left:24px;width:199px;top:300px">Lorem ipsum dolor sit amet, consectetur adipiscing elit, sed do eiusmod tempor incididun.</div>
</div>
<div class="card" style="left:880px;top:1560px;height:392px">
  <div class="photo" style="height:225px;background:linear-gradient(135deg,#f4f4f4,#e6d2c0 50%,#2a3548)" role="img" aria-label="Hand holding a card reading premises liability"></div>
  <svg class="abs" style="left:0;top:188px" width="247" height="40"><polygon points="0,40 123,0 247,40" fill="#f3f3f3"/></svg>
  <div class="abs card-title" style="left:0;width:247px;top:246px">Premises Liability</div>
  <div class="abs card-line" style="left:108px;top:292px"></div>
  <div class="abs card-text" style="left:24px;width:199px;top:300px">Lorem ipsum dolor sit amet, consectetur adipiscing elit, sed do eiusmod tempor incididun.</div>
</div>

<!-- Professionals -->
<div class="abs section-head eyebrow" style="top:2024px;font-size:26px">Our Attorneys</div>
<h2 class="abs section-head" style="top:2055px;font-size:40px;font-weight:700;padding-left:12px">Professionals</h2>
<div class="abs arrows" style="left:1064px;top:2075px"><span>‹</span><span>›</span></div>
<div class="abs" style="left:0;top:2278px;width:1200px;height:346px;background:#1b1b1b"></div>
<svg class="abs" style="left:0;top:2505px" width="1200" height="120" viewBox="0 0 1200 120">
  <polygon points="0,120 600,0 1200,120 1200,120 0,120" fill="#c39300"/>
  <polygon points="0,120 600,26 1200,120" fill="#ffffff"/>
</svg>

<div class="card" style="left:72px;top:2140px;height:320px">
  <div class="photo" style="height:225px;background:linear-gradient(180deg,#c8ccd0,#2c3446)" role="img" aria-label="Portrait of attorney Jack"></div>
  <svg class="abs" style="left:0;top:188px" width="247" height="40"><polygon points="0,40 123,0 247,40" fill="#f3f3f3"/></svg>
  <div class="abs badge" style="left:99px;top:169px;width:40px;height:40px;font-size:18px">›</div>
  <div class="abs card-title" style="left:0;width:247px;top:238px">Jack</div>
  <div class="abs card-text" style="left:0;width:247px;top:260px">Attorney</div>
  <div class="abs card-line" style="left:108px;top:292px"></div>
</div>
<div class="card" style="left:341px;top:2140px;height:320px">
  <div class="photo" style="height:225px;background:linear-gradient(180deg,#9a8a72,#2e2e32)" role="img" aria-label="Portrait of attorney Amith"></div>
  <svg class="abs" style="left:0;top:188px" width="247" height="40"><polygon points="0,40 123,0 247,40" fill="#f3f3f3"/></svg>
  <div class="abs card-title" style="left:0;width:247px;top:238px">Amith</div>
  <div class="abs card-text" style="left:0;width:247px;top:260px">Attorney</div>
  <div class="abs card-line" style="left:108px;top:292px"></div>
</div>
<div class="card" style="left:611px;top:2140px;height:320px">
  <div class="photo" style="height:225px;background:linear-gradient(180deg,#d6d8da,#2a4780)" role="img" aria-label="Portrait of attorney Jhon"></div>
  <svg class="abs" style="left:0;top:188px" width="247" height="40"><polygon points="0,40 123,0 247,40" fill="#f3f3f3"/></svg>
  <div class="abs card-title" style="left:0;width:247px;top:238px">Jhon</div>
  <div class="abs card-text" style="left:0;width:247px;top:260px">Attorney</div>
  <div class="abs card-line" style="left:108px;top:292px"></div>
</div>
<div class="card" style="left:880px;top:2140px;height:320px">
  <div class="photo" style="height:225px;background:linear-gradient(180deg,#7a8a80,#1f2838)" role="img" aria-label="Portrait of attorney Lisa"></div>
  <svg class="abs" style="left:0;top:188px" width="247" height="40"><polygon points="0,40 123,0 247,40" fill="#f3f3f3"/></svg>
  <div class="abs card-title" style="left:0;width:247px;top:238px">Lisa</div>
  <div class="abs card-text" style="left:0;width:247px;top:260px">Attorney</div>
  <div class="abs card-line" style="left:108px;top:292px"></div>
</div>

<!-- Blog -->
<h2 class="abs section-head" style="top:2630px;font-size:40px;font-weight:700">Blog</h2>
<div class="photo" style="left:72px;top:2740px;width:506px;height:285px;background:linear-gradient(135deg,#1e2a36,#5a6f88 55%,#a36a3a)" role="img" aria-label="Judge's gavel striking a toy car"></div>
<div class="photo" style="left:613px;top:2740px;width:507px;height:285px;background:linear-gradient(135deg,#cfd5db,#5a6478 55%,#2a3142)" role="img" aria-label="Legal team meeting around a laptop"></div>
<h3 class="abs blog-title" style="left:76px;top:3050px">Lorem ipsum dolor</h3>
<h3 class="abs blog-title" style="left:620px;top:3050px">Lorem ipsum dolor</h3>
<p class="abs blog-text" style="left:76px;top:3102px;width:480px">Lorem ipsum dolor sit amet, consectetur adipiscing elit, sed do eiusmod tempor incididunt ut labore et dolore magna aliqua. Quis ipsum suspendisse ultrices gravida. Risus commodo viverra maecenas accumsan lacus vel facilisis.</p>
<p class="abs blog-text" style="left:620px;top:3102px;width:480px">Lorem ipsum dolor sit amet, consectetur adipiscing elit, sed do eiusmod tempor incididunt ut labore et dolore magna aliqua. Quis ipsum suspendisse ultrices gravida. Risus commodo viverra maecenas accumsan lacus vel facilisis.</p>
<div class="btn" style="left:76px;top:3237px;width:122px;height:35px;font-size:14px">Learn More</div>
<div class="btn" style="left:620px;top:3237px;width:122px;height:35px;font-size:14px">Learn More</div>

<!-- Footer -->
<div class="abs footer"></div>
<svg class="abs" style="left:0;top:3328px" width="1200" height="130" viewBox="0 0 1200 130">
  <path d="M0,0 Q600,120 1200,0 L1200,2 Q600,60 0,2 Z" fill="#ffffff"/>
  <path d="M0,0 L1200,0 L1200,2 Q600,40 0,2 Z" fill="#ffffff"/>
  <path d="M0,2 Q300,20 600,95 Q900,20 1200,2 L1200,14 Q900,50 600,125 Q300,50 0,14 Z" fill="#c39300"/>
  <path d="M0,0 L1200,0 L1200,2 Q900,20 600,95 Q300,20 0,2 Z" fill="#ffffff"/>
</svg>
<div class="abs" style="left:88px;top:3467px;width:190px;text-align:center;color:#fff">
  <div style="width:28px;height:28px;border:3px solid #fff;margin:0 auto 14px"></div>
  <div style="font-size:34px;font-weight:800;letter-spacing:1px;line-height:1">HAVERLOCK</div>
  <div style="font-size:15px;font-weight:700;letter-spacing:5px;margin-top:6px">TRIAL FIRM</div>
</div>
<div class="abs" style="left:86px;top:3645px;font-size:13px;color:#fff">© 2025 | &nbsp;www.haverlocktrialfirm.com</div>
<div class="abs f-links">
  <div class="active">Home</div><div style="color:#fff">About</div><div style="color:#fff">Practice Area</div><div style="color:#fff">Professionals</div><div style="color:#fff">Resources&amp; Advisers</div><div style="color:#fff">Blog</div>
</div>
<div class="abs f-head" style="left:701px;top:3476px">Address</div>
<div class="abs" style="left:701px;top:3504px;color:#fff;font-size:15px;line-height:22px;display:flex;gap:12px">
  <svg width="12" height="16" viewBox="0 0 12 16" style="margin-top:4px"><path d="M6 0a6 6 0 016 6c0 4-6 10-6 10S0 10 0 6a6 6 0 016-6z" fill="#fff"/><circle cx="6" cy="6" r="2" fill="#111"/></svg>
  <div>#123, Lorium ipsum,<br>Dolor amit,<br>City name.</div>
</div>
<div class="abs" style="left:701px;top:3589px;color:#fff;font-size:15px;display:flex;gap:12px;align-items:center">
  <svg width="14" height="14" viewBox="0 0 24 24"><path fill="#fff" d="M6.6 10.8a15 15 0 006.6 6.6l2.2-2.2a1 1 0 011-.25 11 11 0 003.6.6 1 1 0 011 1V20a1 1 0 01-1 1A17 17 0 013 4a1 1 0 011-1h3.5a1 1 0 011 1 11 11 0 00.6 3.6 1 1 0 01-.25 1z"/></svg>1800-555 0187
</div>
<div class="abs" style="left:701px;top:3622px;color:#fff;font-size:15px;display:flex;gap:12px;align-items:center">
  <svg width="14" height="11" viewBox="0 0 16 12"><rect width="16" height="12" fill="#fff"/><path d="M1 1l7 6 7-6" stroke="#111" fill="none"/></svg>info@haverlocklaw.com
</div>
<div class="abs f-head" style="left:949px;top:3476px">Follow Us</div>
<div class="abs social" style="left:949px;top:3522px"><span></span><span></span><span></span></div>

</body>
</html>
```